Indy Film Production Company/Studio

We need a business card designed from an existing logo. We are a digital studio/production company that caters to creating genre entertainment, like Action, Horror, and martial arts. The card along with the logo will be used to Brand the company from letter heads to banners. The design will also be used for postcards and Brochures. It should be professional and masculine.
Updates

Thank you to all the designers who have participated. I'm narrowing down who it will be. Thank you again.

Target Market(s)

Investors, Networks, Producers, and actors

Industry/Entity Type

Film Production

Contact Information for Business Card

Teodoro Valbuena
Producer/Writer/Director
www.kestrelpicturehouse.example

Requirements
Must have
• Website address, Facebook icon and Twitter icon possibly in the back of the card.
Nice to have
• Logline of Company: Follow The Action.

```html
<!DOCTYPE html>
<html lang="en">
<head>
<meta charset="utf-8">
<title>Kestrel Picture House — Business Card</title>
<link rel="stylesheet" href="https://fonts.googleapis.com/css2?family=Arimo:wght@400;700&display=swap">
<style>
  :root {
    --red: #e01b24;
    --red-deep: #b3121a;
    --ink: #2b2b2b;
    --white: #ffffff;
    --backdrop: #3a3b3e;
  }
  * { box-sizing: border-box; margin: 0; padding: 0; }
  html, body {
    width: 1200px;
    height: 950px;
    overflow: hidden;
    background: var(--backdrop);
    font-family: "Arimo", Arial, sans-serif;
  }
  .canvas {
    position: relative;
    width: 1200px;
    height: 950px;
  }
  .card {
    position: absolute;
    left: 250px;
    width: 700px;
    height: 400px;
    overflow: hidden;
    box-shadow: 0 10px 30px rgba(0,0,0,0.45);
  }
  /* Back of card */
  .card--back {
    top: 55px;
    background: linear-gradient(135deg, var(--red) 0%, var(--red) 55%, var(--red-deep) 100%);
    color: var(--white);
  }
  .social {
    position: absolute;
    top: 24px;
    right: 26px;
    display: flex;
    gap: 6px;
  }
  .social__square {
    width: 26px;
    height: 26px;
    background: var(--white);
    opacity: 0.9;
  }
  .brand-name {
    font-weight: 700;
    letter-spacing: 2px;
    text-transform: uppercase;
    line-height: 1.05;
  }
  .card--back .brand-name {
    position: absolute;
    top: 130px;
    left: 0;
    width: 100%;
    text-align: center;
    font-size: 52px;
    color: var(--white);
  }
  .card--back .website {
    position: absolute;
    top: 262px;
    left: 0;
    width: 100%;
    text-align: center;
    font-size: 20px;
    letter-spacing: 1px;
    color: var(--white);
  }
  /* Front of card */
  .card--front {
    top: 495px;
    background: var(--white);
  }
  .card--front .brand-name {
    position: absolute;
    top: 40px;
    left: 44px;
    font-size: 40px;
    color: var(--red);
  }
  .wave {
    position: absolute;
    inset: 0;
    width: 700px;
    height: 400px;
  }
  .contact {
    position: absolute;
    right: 34px;
    top: 264px;
    text-align: right;
    color: var(--white);
  }
  .contact__name {
    font-size: 24px;
    font-weight: 700;
    line-height: 28px;
  }
  .contact__role {
    font-size: 18px;
    line-height: 22px;
    margin-bottom: 2px;
  }
  .contact__line {
    display: flex;
    justify-content: flex-end;
    align-items: center;
    gap: 8px;
    font-size: 16px;
    line-height: 22px;
  }
  .contact__icon {
    width: 15px;
    height: 15px;
    flex: none;
  }
</style>
</head>
<body>
<main class="canvas">

  <section class="card card--back" aria-label="Business card back">
    <div class="social">
      <span class="social__square" aria-label="Social network"></span>
      <span class="social__square" aria-label="Social network"></span>
    </div>
    <p class="brand-name">Kestrel Picture House</p>
    <p class="website">www.kestrelpicturehouse.example</p>
  </section>

  <section class="card card--front" aria-label="Business card front">
    <p class="brand-name">Kestrel<br>Picture House</p>

    <svg class="wave" viewBox="0 0 700 400" aria-hidden="true">
      <path fill="#2b2b2b" d="M0,165 C150,150 280,215 400,215 C520,215 620,160 700,130 L700,150 C620,182 520,236 400,236 C280,236 150,185 0,185 Z"/>
      <path fill="#e01b24" d="M0,205 C150,195 280,250 400,250 C520,250 620,195 700,170 L700,400 L0,400 Z"/>
      <path fill="none" stroke="#ffffff" stroke-width="3" d="M0,232 C160,225 290,275 410,272 C530,268 630,215 700,196"/>
    </svg>

    <div class="contact">
      <p class="contact__name">Teodoro Valbuena</p>
      <p class="contact__role">Producer/Writer/Director</p>
      <p class="contact__line">555 0142 7781
        <svg class="contact__icon" viewBox="0 0 16 16" aria-hidden="true"><path fill="#fff" d="M3 2h3l1 3-2 1.5c.8 1.8 2.2 3.2 4 4L10.5 8.5l3 1v3c0 .8-.7 1.5-1.5 1.5C6.5 14 2 9.5 2 4c0-.8.7-2 1-2z"/></svg>
      </p>
      <p class="contact__line">teo@kestrelpicturehouse.example
        <svg class="contact__icon" viewBox="0 0 16 16" aria-hidden="true"><rect x="1" y="3" width="14" height="10" fill="#fff"/><path d="M1 3l7 6 7-6" fill="none" stroke="#e01b24" stroke-width="1.4"/></svg>
      </p>
      <p class="contact__line">www.kestrelpicturehouse.example
        <svg class="contact__icon" viewBox="0 0 16 16" aria-hidden="true"><circle cx="8" cy="8" r="7" fill="#fff"/><path d="M1 8h14M8 1c-3 3.5-3 10.5 0 14M8 1c3 3.5 3 10.5 0 14" fill="none" stroke="#e01b24" stroke-width="1"/></svg>
      </p>
    </div>
  </section>

</main>
</body>
</html>
```